Business Post Card/ Handout design

Looking to have this design edited and updated to look a little more eye catching.
As well DECLUTTER remove Contractor Pricing / Remove the 24 hour guarantee and the pick up 7 days a week.
Under 16 yard change it to only say Starting at 300.00 / 20 Yard Starting at 450.00 / 30 Yard Starting at 600.00 / and please add 40 Yard starting at 750.00
Please remove the white letters under the prices that say brush only and Make a new box or area that says Brush Dumpsters available.
Remove concrete/ shingles only from under the 20 yard box.
Please just try to clean it up and make it look nice and eye catching use whatever font you want. Keep all colors same
Look and feel
Each slider illustrates characteristics of the customer's brand and the style your logo design should communicate.

```html
<!DOCTYPE html>
<html lang="en">
<head>
<meta charset="utf-8">
<title>Boundless Bins – Dumpster Rental Flyer</title>
<link href="https://fonts.googleapis.com/css2?family=Anton&family=Montserrat:wght@500;600;700&display=swap" rel="stylesheet">
<style>
  :root {
    --purple: #6f3696;
    --ink: #000000;
    --paper: #ffffff;
    --page: #ffffff;
  }
  html, body {
    margin: 0;
    width: 1200px;
    height: 1200px;
    overflow: hidden;
    background: var(--page);
  }
  .flyer {
    position: absolute;
    left: 167px;
    top: 40px;
    width: 1000px;
    height: 1295px;
    transform: scale(0.865);
    transform-origin: 0 0;
    background: var(--paper);
    outline: 5px solid var(--ink);
    outline-offset: -5px;
    overflow: hidden;
    font-family: "Montserrat", sans-serif;
  }
  .flyer-shapes {
    position: absolute;
    left: 0;
    top: 0;
    width: 1000px;
    height: 1295px;
  }
  .brand-name {
    position: absolute;
    right: 52px;
    top: 70px;
    margin: 0;
    font-family: "Montserrat", sans-serif;
    font-weight: 700;
    font-size: 50px;
    line-height: 1;
    color: var(--paper);
    letter-spacing: 1px;
  }
  .headline {
    position: absolute;
    left: 0;
    right: 0;
    top: 720px;
    margin: 0;
    text-align: center;
    font-family: "Anton", sans-serif;
    font-weight: 400;
    font-size: 82px;
    line-height: 1;
    color: var(--paper);
    -webkit-text-stroke: 5px var(--ink);
    paint-order: stroke fill;
    letter-spacing: -1px;
  }
  .price-box {
    position: absolute;
    width: 298px;
    height: 86px;
    box-sizing: border-box;
    background: var(--purple);
    border: 3px solid var(--ink);
    border-radius: 10px;
    color: var(--paper);
    font-family: "Anton", sans-serif;
  }
  .price-box .size {
    position: absolute;
    left: 16px;
    top: 8px;
    font-size: 37px;
    line-height: 1;
  }
  .price-box .label {
    position: absolute;
    left: 16px;
    top: 49px;
    font-size: 23px;
    line-height: 1;
  }
  .price-box .price {
    position: absolute;
    right: 16px;
    top: 20px;
    font-size: 40px;
    line-height: 1;
  }
  .box-16 { left: 118px; top: 905px; }
  .box-20 { left: 586px; top: 905px; }
  .box-30 { left: 118px; top: 1022px; }
  .box-40 { left: 586px; top: 1022px; }
  .brush-banner {
    position: absolute;
    left: 0;
    right: 0;
    top: 1137px;
    height: 49px;
    margin: 0;
    display: flex;
    align-items: center;
    justify-content: center;
    font-weight: 600;
    font-size: 36px;
    line-height: 1;
    color: var(--paper);
  }
  .contact {
    position: absolute;
    left: 0;
    right: 0;
    top: 1205px;
    margin: 0;
    text-align: center;
    font-weight: 600;
    font-size: 16px;
    line-height: 23px;
    color: var(--ink);
  }
</style>
</head>
<body>
  <main class="flyer">
    <svg class="flyer-shapes" viewBox="0 0 1000 1295">
      <defs>
        <linearGradient id="photoTone" x1="0" y1="0" x2="0" y2="1">
          <stop offset="0" stop-color="#8fb8df"/>
          <stop offset="0.25" stop-color="#4f7a3a"/>
          <stop offset="0.55" stop-color="#b9b7c0"/>
          <stop offset="1" stop-color="#a39580"/>
        </linearGradient>
      </defs>
      <polygon class="hero-photo" role="img"
        aria-label="Photo of a white roll-off truck carrying a purple dumpster at a job site, with a smiling worker in hard hat and safety vest"
        points="0,0 1000,0 1000,705 500,900 0,705" fill="url(#photoTone)"/>
      <polygon class="chevron-band" points="0,700 500,895 1000,700 1000,728 500,905 0,728" fill="var(--purple)"/>
      <polygon class="pointer-top" points="500,640 536,770 556,820 500,866 444,820 464,770" fill="var(--purple)"/>
      <polygon class="pointer-center" points="500,911 554,970 500,1126 446,970" fill="var(--purple)"/>
      <g class="corner-shards" fill="var(--ink)">
        <polygon points="24,738 66,782 24,822"/>
        <polygon points="100,782 156,818 118,822"/>
        <polygon points="24,860 76,800 94,864"/>
        <polygon points="118,845 156,836 156,862"/>
        <polygon points="976,738 934,782 976,822"/>
        <polygon points="900,782 844,818 882,822"/>
        <polygon points="976,860 924,800 906,864"/>
        <polygon points="882,845 844,836 844,862"/>
      </g>
      <path class="brush-pill" fill="var(--ink)"
        d="M170,1137 H834 Q848,1137 846,1150 L838,1161 L846,1172 Q848,1186 834,1186 H170 Q156,1186 158,1172 L166,1161 L158,1150 Q156,1137 170,1137 Z"/>
      <g class="footer-shards" fill="var(--purple)">
        <polygon points="24,1216 24,1268 62,1244"/>
        <polygon points="60,1240 94,1230 94,1262 60,1262"/>
        <polygon points="50,1216 70,1216 60,1226"/>
        <polygon points="976,1216 976,1268 938,1244"/>
        <polygon points="940,1240 906,1230 906,1262 940,1262"/>
        <polygon points="950,1216 930,1216 940,1226"/>
      </g>
    </svg>

    <p class="brand-name">BOUNDLESS BINS</p>
    <h1 class="headline">DUMPSTER RENTAL</h1>

    <div class="price-box box-16"><span class="size">16 YARD</span><span class="label">STARTING AT</span><span class="price">$300</span></div>
    <div class="price-box box-20"><span class="size">20 YARD</span><span class="label">STARTING AT</span><span class="price">$450</span></div>
    <div class="price-box box-30"><span class="size">30 YARD</span><span class="label">STARTING AT</span><span class="price">$600</span></div>
    <div class="price-box box-40"><span class="size">40 YARD</span><span class="label">STARTING AT</span><span class="price">$750</span></div>

    <p class="brush-banner">Brush Dumpsters Available</p>

    <p class="contact">Call or Email to Schedule<br>865-555-0142 &nbsp;|&nbsp; INFO@BOUNDLESSBINS.COM<br>WWW.BOUNDLESSBINS.COM</p>
  </main>
</body>
</html>
```